Home Security Company Business Card

Looking for a eye catching business card that is non traditional and stands out but yet still looks professional. It should include all the pertinent information such as name, title, address, telephone, e-mail, website address should definitely stand out and then finally the logo.

Target Market(s)

Residential and Commercial accounts mostly upscale accounts

Industry/Entity Type

Security

Contact Information for Business Card

Name
Title
Address
Office #
Cell #
E-mail
Website

Font styles to use
Serif
Sans Serif

Requirements
Must have
• Logo, two sided color configuration
Nice to have
• You decide
Should not have
• There really aren't any.

```html
<!DOCTYPE html>
<html lang="en">
<head>
<meta charset="utf-8">
<title>Ironvale Protection Inc. – Business Card</title>
<link href="https://fonts.googleapis.com/css2?family=Open+Sans:wght@400;600;700&display=swap" rel="stylesheet">
<style>
  :root {
    --page: #ecebe8;
    --red-light: #a8303f;
    --red: #8c1a26;
    --red-dark: #5e0d16;
    --copper: #b8683c;
    --copper-dark: #8f3f22;
    --gold: #f0b23a;
    --white: #ffffff;
  }
  * { margin: 0; padding: 0; box-sizing: border-box; }
  html, body { width: 1200px; height: 913px; overflow: hidden; }
  body {
    background: var(--page);
    font-family: "Open Sans", Arial, sans-serif;
    position: relative;
  }
  .card {
    position: absolute;
    width: 540px;
    height: 310px;
    border-radius: 18px;
    overflow: hidden;
    background: linear-gradient(160deg, var(--red-light) 0%, var(--red) 50%, var(--red-dark) 100%);
    box-shadow: 0 10px 30px rgba(0,0,0,.25);
    color: var(--white);
  }
  .card--front { left: 40px; top: 180px; }
  .card--back { left: 620px; top: 420px; }

  .front-art { position: absolute; inset: 0; }

  .brand {
    position: absolute;
    display: flex;
    align-items: center;
    gap: 10px;
    color: var(--white);
    font-weight: 600;
    white-space: nowrap;
  }
  .brand__dot {
    border-radius: 50%;
    background: var(--gold);
    flex: none;
  }
  .card--front .brand { right: 40px; top: 44px; font-size: 17px; }
  .card--front .brand__dot { width: 34px; height: 34px; }

  .divider {
    position: absolute;
    left: 150px; right: 30px; top: 98px;
    height: 1px;
    background: rgba(255,255,255,.75);
  }

  .contact {
    position: absolute;
    right: 30px; top: 114px;
    text-align: right;
    font-size: 14px;
    line-height: 21px;
    white-space: nowrap;
  }
  .contact__address { color: var(--gold); }
  .contact__row { display: flex; justify-content: flex-end; align-items: center; gap: 6px; }
  .contact__row svg { width: 12px; height: 12px; flex: none; }
  .contact__email { margin-top: 18px; }

  .person {
    position: absolute;
    left: 24px; bottom: 40px;
    white-space: nowrap;
  }
  .person__name { font-size: 24px; font-weight: 700; line-height: 1.1; }
  .person__title { font-size: 15px; color: var(--gold); margin-top: 2px; }
  .person-rule {
    position: absolute;
    left: 90px; width: 200px; bottom: 50px;
    height: 1px;
    background: rgba(255,255,255,.75);
  }

  .card--back .brand {
    left: 50%; top: 110px;
    transform: translateX(-50%);
    font-size: 24px;
  }
  .card--back .brand__dot { width: 48px; height: 48px; }

  .web-band {
    position: absolute;
    left: 0; right: 0; bottom: 42px;
    height: 34px;
    background: var(--white);
    display: flex;
    align-items: center;
    justify-content: space-between;
    padding: 0 16px;
  }
  .web-band__url {
    color: var(--red-dark);
    font-size: 15px;
    font-weight: 700;
  }
  .web-band svg { width: 60px; height: 18px; flex: none; }
</style>
</head>
<body>

  <section class="card card--front" aria-label="Business card front">
    <svg class="front-art" viewBox="0 0 540 310" preserveAspectRatio="none" aria-hidden="true">
      <polygon points="0,60 130,60 360,310 0,310" fill="var(--copper)"/>
      <polygon points="120,310 190,205 270,310" fill="var(--red-dark)"/>
      <polygon points="0,200 60,200 0,260" fill="var(--copper-dark)" opacity=".5"/>
    </svg>

    <div class="brand"><span class="brand__dot"></span>Ironvale Protection Inc.</div>
    <div class="divider"></div>

    <div class="contact">
      <div class="contact__address">742 Linden Avenue<br>Aurora, Illinois 60505</div>
      <div class="contact__row">+330 5510-2846
        <svg viewBox="0 0 12 12"><rect x="1" y="5" width="10" height="6" rx="1" fill="var(--gold)"/><path d="M1 5 Q6 0 11 5" stroke="var(--gold)" stroke-width="1.6" fill="none"/></svg>
      </div>
      <div class="contact__row">+3307718-40263
        <svg viewBox="0 0 12 12"><path d="M2 1 L4.5 1 L5.5 3.5 L4 5 Q5 7.5 7 8 L8.5 6.5 L11 7.5 L11 10 Q6 11.5 2 6 Q1 3 2 1 Z" fill="var(--gold)"/></svg>
      </div>
      <div class="contact__row contact__email">info@danielharwickmail.com
        <svg viewBox="0 0 12 12"><rect x="1" y="2.5" width="10" height="7" fill="none" stroke="var(--gold)" stroke-width="1.2"/><path d="M1 2.5 L6 7 L11 2.5" fill="none" stroke="var(--gold)" stroke-width="1.2"/></svg>
      </div>
    </div>

    <div class="person-rule"></div>
    <div class="person">
      <div class="person__name">Daniel Harwick</div>
      <div class="person__title">Owner</div>
    </div>
  </section>

  <section class="card card--back" aria-label="Business card back">
    <div class="brand"><span class="brand__dot"></span>Ironvale Protection Inc.</div>
    <div class="web-band">
      <svg viewBox="0 0 60 18" aria-hidden="true">
        <polygon points="0,0 12,9 0,18" fill="var(--red-dark)"/>
        <polygon points="20,0 32,9 20,18" fill="var(--red-dark)"/>
        <polygon points="40,0 52,9 40,18" fill="var(--red-dark)"/>
      </svg>
      <span class="web-band__url">www.ironvaleprotectioninc.com</span>
      <svg viewBox="0 0 60 18" aria-hidden="true">
        <polygon points="20,0 8,9 20,18" fill="var(--red-dark)"/>
        <polygon points="40,0 28,9 40,18" fill="var(--red-dark)"/>
        <polygon points="60,0 48,9 60,18" fill="var(--red-dark)"/>
      </svg>
    </div>
  </section>

</body>
</html>
```